KAJU Freightways #ALLKAJU Business Cards & Letterhead

I am looking to business cards designed for our organization. We are currently undergoing a small re-branding that is taking place. Our organization is called KAJU Freightways and we are headquartered in Phoenix, AZ. We primarily provide transportation and logistics services to the Marlow Parcel Bureau who is our largest customer. I would like to see a design that incorporates name, title, contact info, website, and address (this will be different depending on the employee). I would also like to see some color on the business card using our logo colors or a variation. I would like our logo on the back of the business card with the website displayed. The final design should communicate that we are a next generation transportation operate that focuses on being driver-first, customer-centric, innovative, and sustainable.We would also like our #ALLKAJU catch phrase incorporated as well.

Target Market(s)

Transportation & Logistics

Industry/Entity Type

Trucking Company

Contact Information for Business Card

-First and Last Name
-Position Title
-Contact Phone
-Contact Email
-Physical Address

Font styles to use
Serif

Colors

Designer to choose colors to be used in the design.

Requirements
Must have
• -KAJU logo prominently displayed
• -#ALLKAJU catch phrase used
• -Some amount of color, design gradient, etc.
• -Logo on the back with website listed (https://www.kajufreightco.example)

```html
<!DOCTYPE html>
<html lang="en">
<head>
<meta charset="utf-8">
<title>KAJU Freightways – Business Card</title>
<link rel="stylesheet" href="https://fonts.googleapis.com/css2?family=Montserrat:wght@400;500&family=Playfair+Display:wght@600&display=swap">
<style>
  :root {
    --backdrop: #1a1a1a;
    --card-edge: #242424;
    --silver: #bdbdbd;
    --silver-soft: #9a9a9a;
    --accent: #3fa9c9;
    --accent-deep: #2b6fb0;
  }
  * { margin: 0; padding: 0; box-sizing: border-box; }
  html, body { width: 1200px; height: 900px; overflow: hidden; }
  body {
    background: var(--backdrop);
    display: flex;
    flex-direction: column;
    align-items: center;
    justify-content: center;
    gap: 32px;
    font-family: "Montserrat", sans-serif;
    color: var(--silver);
  }
  .card {
    position: relative;
    width: 610px;
    height: 349px;
    background: linear-gradient(160deg, #141414 0%, #1b1b1b 60%, #252525 100%);
    border: 1px solid var(--card-edge);
    overflow: hidden;
  }
  .card::after {
    content: "";
    position: absolute;
    left: 0; right: 0; bottom: 0;
    height: 4px;
    background: linear-gradient(90deg, var(--accent-deep), var(--accent));
  }
  /* Front */
  .card-front .brand {
    position: absolute;
    left: 0; right: 0;
    top: 108px;
    display: flex;
    align-items: center;
    justify-content: center;
    gap: 14px;
  }
  .card-front .brand-dot {
    width: 16px;
    height: 16px;
    border-radius: 50%;
    background: var(--accent);
  }
  .card-front .brand-name {
    font-family: "Playfair Display", serif;
    font-weight: 600;
    font-size: 60px;
    line-height: 1;
    letter-spacing: 3px;
    color: var(--silver);
  }
  .card-front .tagline {
    position: absolute;
    left: 0; right: 0;
    top: 196px;
    text-align: center;
    font-size: 15px;
    font-weight: 500;
    letter-spacing: 4px;
    color: var(--accent);
  }
  .card-front .site {
    position: absolute;
    left: 0; right: 0;
    bottom: 40px;
    text-align: center;
    font-size: 17px;
    letter-spacing: 2px;
    color: var(--silver-soft);
  }
  /* Back */
  .card-back .identity {
    position: absolute;
    right: 330px;
    top: 118px;
    text-align: right;
  }
  .card-back .person-name {
    font-family: "Playfair Display", serif;
    font-weight: 600;
    font-size: 30px;
    letter-spacing: 1px;
    text-transform: uppercase;
    line-height: 1.15;
    color: var(--silver);
  }
  .card-back .person-title {
    font-size: 16px;
    color: var(--silver-soft);
    margin-top: 4px;
  }
  .card-back .divider {
    position: absolute;
    left: 300px;
    top: 120px;
    width: 2px;
    height: 72px;
    background: linear-gradient(180deg, var(--accent), var(--accent-deep));
  }
  .card-back .contact {
    position: absolute;
    left: 322px;
    top: 120px;
    list-style: none;
  }
  .card-back .contact li {
    display: flex;
    align-items: center;
    gap: 10px;
    font-size: 16px;
    line-height: 27px;
    color: var(--silver);
  }
  .card-back .contact svg { width: 12px; height: 12px; flex: none; }
  .card-back .address {
    position: absolute;
    left: 0; right: 0;
    bottom: 36px;
    text-align: center;
    font-size: 16px;
    letter-spacing: 0.5px;
    color: var(--silver-soft);
  }
</style>
</head>
<body>
  <section class="card card-front" aria-label="Card front">
    <div class="brand">
      <span class="brand-dot" aria-hidden="true"></span>
      <span class="brand-name">KAJU</span>
    </div>
    <p class="tagline">#ALLKAJU</p>
    <p class="site">www.kajufreightco.example</p>
  </section>

  <section class="card card-back" aria-label="Card back">
    <div class="identity">
      <h1 class="person-name">Daniel Orwin</h1>
      <p class="person-title">Director</p>
    </div>
    <div class="divider"></div>
    <ul class="contact">
      <li>
        <svg viewBox="0 0 12 12" aria-hidden="true"><path d="M3 1l2 2.5-1.2 1.2c.6 1.4 1.7 2.5 3.1 3.1L8.1 6.6 10.6 8.6 9.4 10.6C5 10.3 1.7 7 1.4 2.6z" fill="var(--accent)"/></svg>
        555-014-2290
      </li>
      <li>
        <svg viewBox="0 0 12 12" aria-hidden="true"><rect x="1" y="2.5" width="10" height="7" fill="none" stroke="var(--accent)" stroke-width="1.2"/><path d="M1 2.8l5 3.7 5-3.7" fill="none" stroke="var(--accent)" stroke-width="1.2"/></svg>
        info@kajufreightco.example
      </li>
      <li>
        <svg viewBox="0 0 12 12" aria-hidden="true"><circle cx="6" cy="6" r="4.8" fill="none" stroke="var(--accent)" stroke-width="1.1"/><ellipse cx="6" cy="6" rx="2" ry="4.8" fill="none" stroke="var(--accent)" stroke-width="1"/><path d="M1.2 6h9.6" stroke="var(--accent)" stroke-width="1"/></svg>
        www.kajufreightco.example
      </li>
    </ul>
    <p class="address">4170 North Saguaro Crest Drive Phoenix, AZ 85016</p>
  </section>
</body>
</html>
```